Flyer-Design für Fahrzeugpflege&Lackveredelung
Zielgruppe
Die Firma KM Autoglanz - Fahrzeugpflege&Lackveredelung ist ein Kleinunternehmen im Car-Detailing Bereich. Hier steht höchste Qualität und maximale Kundenzufriedenheit auf höchster Stelle.
Zielgruppen sind Fahrzeugbesitzer von hochwertigen Wagen, die höchste Ansprüche auf die Fahrzeugaufbereitung legen.
Aber auch das Tagesgeschäft mit Innenraumaufbereitungen für den Normalverbraucher sind möglich.
Aufgabenstellung
Der Flyer soll modern und hochwertig aussehen.
Größe des Flyers: DIN lang (9,8x21)
2-seitig 4/4 farbig
Farben, Daten und Co bitte auf der Internetseite entnehmen
www.kmautoglanz-beispiel.de

```html
<!DOCTYPE html>
<html lang="de">
<head>
<meta charset="utf-8">
<title>KM Autoglanz – Flyer DIN lang</title>
<link href="https://fonts.googleapis.com/css2?family=Raleway:wght@400;500;600;700;800;900&display=swap" rel="stylesheet">
<style>
  :root {
    --page-bg: #e8e9eb;
    --paper: #ffffff;
    --ink-dark: #0a0b0f;
    --ink-grey: #4d4e50;
    --brand-blue: #2f6fba;
    --photo-dark: #2a2622;
    --text-white: #ffffff;
  }
  * { margin: 0; padding: 0; box-sizing: border-box; }
  html, body {
    width: 1154px; height: 1200px; overflow: hidden;
    background: var(--page-bg);
    font-family: "Raleway", Arial, sans-serif;
  }
  .canvas { position: relative; width: 1154px; height: 1200px; }
  .flyer-side {
    position: absolute; top: 29px; width: 532px; height: 1141px;
    background: var(--paper); overflow: hidden;
  }
  .flyer-side--front { left: 29px; }
  .flyer-side--back { left: 592px; }
  .flyer-side svg { display: block; width: 532px; height: 1141px; }
  .t-grey { fill: var(--ink-grey); }
  .t-blue { fill: var(--brand-blue); }
  .t-white { fill: var(--text-white); }
  .headline { font-weight: 900; font-size: 108px; }
  .service-item { font-weight: 500; font-size: 32px; }
  .brand-name { font-weight: 500; font-size: 38px; fill: var(--text-white); }
  .brand-sub { font-weight: 500; font-size: 22px; fill: var(--text-white); letter-spacing: 5px; }
  .web { font-weight: 600; font-size: 24px; }
  .tile-label { font-weight: 700; font-size: 28px; fill: var(--text-white); paint-order: stroke; stroke: rgba(0,0,0,.35); stroke-width: 3px; }
  .back-title { font-weight: 900; font-size: 50px; }
  .more-label { font-weight: 500; font-size: 24px; }
  .more-list { font-weight: 700; font-size: 21px; }
  .price-label { font-weight: 800; font-size: 24px; }
  .price { font-weight: 800; font-size: 150px; letter-spacing: -4px; }
  .price-note { font-weight: 400; font-size: 15px; }
  .contact { font-weight: 500; font-size: 26px; fill: var(--text-white); }
</style>
</head>
<body>
<div class="canvas">

  <!-- Front side -->
  <section class="flyer-side flyer-side--front">
    <svg viewBox="0 0 870 1864" xmlns="http://www.w3.org/2000/svg">
      <defs>
        <linearGradient id="g-car-dark" x1="0" y1="0" x2="1" y2="1">
          <stop offset="0" stop-color="#1b1c20"/>
          <stop offset=".5" stop-color="#8a8d94"/>
          <stop offset="1" stop-color="#15161a"/>
        </linearGradient>
        <linearGradient id="g-polish" x1="0" y1="0" x2="1" y2="1">
          <stop offset="0" stop-color="#5a4a3e"/>
          <stop offset=".45" stop-color="#2a2420"/>
          <stop offset=".75" stop-color="#1a1716"/>
          <stop offset="1" stop-color="#0e0d0d"/>
        </linearGradient>
        <radialGradient id="g-white-car" cx=".6" cy=".55" r=".6">
          <stop offset="0" stop-color="#c9cbcf"/>
          <stop offset=".6" stop-color="#eceded"/>
          <stop offset="1" stop-color="#ffffff"/>
        </radialGradient>
      </defs>

      <polygon points="0,0 870,0 870,917 0,492" fill="var(--ink-dark)"/>
      <polygon role="img" aria-label="Foto: Front eines silbernen Sportwagens im Dunkeln" points="0,75 220,95 300,380 240,520 0,420" fill="url(#g-car-dark)" opacity=".85"/>

      <polygon points="85,488 150,356 335,312 392,332 130,500" fill="none" stroke="#fff" stroke-width="3"/>
      <polygon points="623,305 865,422 621,826 589,820" fill="var(--brand-blue)"/>
      <polygon role="img" aria-label="Foto: Polieren eines Scheinwerfers mit Poliermaschine" points="49,640 575,289 823,432 533,900" fill="url(#g-polish)" stroke="#fff" stroke-width="3"/>
      <polygon points="460,780 702,622 815,690 735,820" fill="none" stroke="#fff" stroke-width="2.5"/>

      <text class="brand-name" x="668" y="147" text-anchor="middle">KM AUTOGLANZ</text>
      <text class="brand-sub" x="668" y="175" text-anchor="middle">Fahrzeugpflege</text>
      <text class="brand-sub" x="668" y="198" text-anchor="middle" style="letter-spacing:1.5px">Lackveredelung</text>

      <rect role="img" aria-label="Foto: weißer Sportwagen mit Felgen, Seitenansicht" x="430" y="1270" width="440" height="594" fill="url(#g-white-car)"/>

      <text class="headline t-grey" x="78" y="1012" textLength="512" lengthAdjust="spacingAndGlyphs">THE ONLY</text>
      <text class="headline t-blue" x="78" y="1104" textLength="733" lengthAdjust="spacingAndGlyphs">CAR DETAILER</text>
      <text class="headline t-grey" x="78" y="1195" textLength="553" lengthAdjust="spacingAndGlyphs">YOU NEED.</text>

      <g class="service-list">
        <g transform="translate(0,1307)">
          <polygon points="84,-4 100,-22 128,-16 114,8" fill="var(--brand-blue)"/>
          <text class="service-item t-grey" x="152" y="0">Keramikbeschichtung</text>
        </g>
        <g transform="translate(0,1382)">
          <polygon points="84,-4 100,-22 128,-16 114,8" fill="var(--brand-blue)"/>
          <text class="service-item t-grey" x="152" y="0">Lackkorrektur</text>
        </g>
        <g transform="translate(0,1458)">
          <polygon points="84,-4 100,-22 128,-16 114,8" fill="var(--brand-blue)"/>
          <text class="service-item t-grey" x="152" y="0">Innenraumaufbereitung</text>
        </g>
        <g transform="translate(0,1534)">
          <polygon points="84,-4 100,-22 128,-16 114,8" fill="var(--brand-blue)"/>
          <text class="service-item t-grey" x="152" y="0">Lederpflege <tspan class="t-blue">&amp;</tspan> Reparatur</text>
        </g>
        <g transform="translate(0,1610)">
          <polygon points="84,-4 100,-22 128,-16 114,8" fill="var(--brand-blue)"/>
          <text class="service-item t-grey" x="152" y="0">Scheibenversiegelung</text>
        </g>
      </g>

      <text class="web t-blue" x="88" y="1742">www.kmautoglanz-beispiel.de</text>
    </svg>
  </section>

  <!-- Back side -->
  <section class="flyer-side flyer-side--back">
    <svg viewBox="0 0 869 1864" xmlns="http://www.w3.org/2000/svg">
      <defs>
        <linearGradient id="g-paint" x1="0" y1="0" x2="1" y2="1"><stop offset="0" stop-color="#4a4b4d"/><stop offset="1" stop-color="#1e1f21"/></linearGradient>
        <linearGradient id="g-coat" x1="0" y1="0" x2="1" y2="1"><stop offset="0" stop-color="#6c6f74"/><stop offset="1" stop-color="#141518"/></linearGradient>
        <linearGradient id="g-interior" x1="0" y1="0" x2="1" y2="1"><stop offset="0" stop-color="#3b3c3e"/><stop offset="1" stop-color="#161718"/></linearGradient>
        <linearGradient id="g-seat" x1="0" y1="0" x2="1" y2="1"><stop offset="0" stop-color="#a8a49c"/><stop offset="1" stop-color="#6c6963"/></linearGradient>
        <linearGradient id="g-leather" x1="0" y1="0" x2="1" y2="1"><stop offset="0" stop-color="#4e4f52"/><stop offset="1" stop-color="#1a1b1d"/></linearGradient>
        <linearGradient id="g-red-car" x1="0" y1="0" x2="1" y2="1"><stop offset="0" stop-color="#e8333a"/><stop offset="1" stop-color="#7a0f14"/></linearGradient>
        <g id="tile-band"><polygon points="250,5 355,58 245,235 232,228 335,60" fill="var(--brand-blue)"/></g>
      </defs>

      <text class="back-title t-grey" x="52" y="104">WAS KANN ICH FÜR</text>
      <text class="back-title" x="52" y="144"><tspan class="t-blue">DEIN FAHRZEUG</tspan><tspan class="t-grey"> TUN?</tspan></text>

      <text x="748" y="102" text-anchor="middle" style="font-weight:500;font-size:24px;fill:var(--ink-grey)">KM AUTOGLANZ</text>
      <text x="748" y="122" text-anchor="middle" style="font-weight:500;font-size:13px;letter-spacing:3px;fill:var(--ink-grey)">Fahrzeugpflege</text>
      <text x="748" y="136" text-anchor="middle" style="font-weight:500;font-size:13px;letter-spacing:1px;fill:var(--ink-grey)">Lackveredelung</text>

      <g transform="translate(72,189)">
        <use href="#tile-band"/>
        <polygon role="img" aria-label="Foto: Lackoberfläche vor und nach der Korrektur" points="0,150 55,28 230,0 340,60 215,265" fill="url(#g-paint)"/>
        <text class="tile-label" x="170" y="131" text-anchor="middle">Lackkorrektur</text>
      </g>
      <g transform="translate(444,189)">
        <use href="#tile-band"/>
        <polygon role="img" aria-label="Foto: versiegelter schwarzer Lack mit Felge" points="0,150 55,28 230,0 340,60 215,265" fill="url(#g-coat)"/>
        <text class="tile-label" x="170" y="131" text-anchor="middle">Lackveredelung</text>
      </g>
      <g transform="translate(72,502)">
        <use href="#tile-band"/>
        <polygon role="img" aria-label="Foto: gereinigtes Armaturenbrett" points="0,150 55,28 230,0 340,60 215,265" fill="url(#g-interior)"/>
        <text class="tile-label" x="170" y="131" text-anchor="middle">Innenraumreinigung</text>
      </g>
      <g transform="translate(444,502)">
        <use href="#tile-band"/>
        <polygon role="img" aria-label="Foto: Stoffsitz vor und nach der Reinigung" points="0,150 55,28 230,0 340,60 215,265" fill="url(#g-seat)"/>
        <text class="tile-label" x="170" y="131" text-anchor="middle">Polsterreinigung</text>
      </g>
      <g transform="translate(72,815)">
        <use href="#tile-band"/>
        <polygon role="img" aria-label="Foto: gepflegter Ledersitz" points="0,150 55,28 230,0 340,60 215,265" fill="url(#g-leather)"/>
        <text class="tile-label" x="170" y="131" text-anchor="middle">Lederreinigung</text>
      </g>
      <g transform="translate(444,815)">
        <use href="#tile-band"/>
        <polygon role="img" aria-label="Foto: reparierte Lederwange eines Sitzes" points="0,150 55,28 230,0 340,60 215,265" fill="url(#g-leather)"/>
        <text class="tile-label" x="170" y="131" text-anchor="middle">Lederreparatur</text>
      </g>

      <text class="more-label t-grey" x="435" y="1132" text-anchor="middle">Weitere Leistungen:</text>
      <text class="more-list t-blue" x="435" y="1159" text-anchor="middle">Scheibenversiegelung, Bremsenversiegelung, Wachs-Versiegelung,</text>
      <text class="more-list t-blue" x="435" y="1185" text-anchor="middle">Cabriodachimprägnierung, Scheinwerferaufbereitung, uvm.</text>

      <text class="price-label t-grey" x="435" y="1245" text-anchor="middle">AUSSENAUFBEREITUNG AB</text>
      <text class="price t-blue" x="305" y="1360">299<tspan style="font-size:72px;letter-spacing:0">€</tspan></text>
      <text class="t-blue" x="520" y="1295" style="font-size:30px;font-weight:700">*</text>
      <text class="price-note t-grey" x="435" y="1392" text-anchor="middle">*Alle Preise orientieren sich an</text>
      <text class="price-note t-grey" x="435" y="1411" text-anchor="middle">einem gepflegten Fahrzeug</text>
      <text class="price-note t-grey" x="435" y="1430" text-anchor="middle">im Neuwagenzustand.</text>

      <polygon points="0,1337 869,1782 869,1864 0,1864" fill="var(--brand-blue)"/>
      <polygon role="img" aria-label="Foto: Front eines Fahrzeugs, blau eingefärbt" points="0,1420 440,1640 440,1864 0,1864" fill="#3a78c0" opacity=".5"/>
      <polygon points="440,1570 869,1752 869,1782 440,1592" fill="#3c3c3e"/>
      <path role="img" aria-label="Foto: roter Sportwagen, Frontansicht" d="M450,1590 C480,1480 600,1440 869,1430 L869,1752 Z" fill="url(#g-red-car)"/>

      <text class="contact" x="65" y="1557" style="font-weight:600">Inh. Markus Kellner</text>
      <text class="contact" x="65" y="1604">Musterweg 7</text>
      <text class="contact" x="65" y="1635">34500 Beispielstadt</text>
      <g transform="translate(65,1664)" fill="#fff">
        <path d="M4,2 C2,2 0,4 1,7 C3,15 10,22 18,24 C21,25 23,23 23,21 L23,18 L17,15 L14,18 C10,16 7,13 6,9 L9,6 L6,1 Z"/>
      </g>
      <text class="contact" x="105" y="1686">+49 170 000 1234</text>
      <g transform="translate(65,1716)" fill="none" stroke="#fff" stroke-width="2.5">
        <rect x="1" y="1" width="24" height="18" fill="#fff" stroke="none"/>
        <path d="M1,1 L13,11 L25,1" stroke="var(--brand-blue)"/>
      </g>
      <text class="contact" x="105" y="1734">info@kmautoglanz-beispiel.de</text>
      <text class="contact" x="65" y="1811" style="font-weight:600">www.kmautoglanz-beispiel.de</text>
    </svg>
  </section>

</div>
</body>
</html>
```